American cannabis tech company business card design

Pavrel.com is seeking a modern, professional, and brand-aligned business card that represents our company and its core values: Mission, Story, Values, and Impact. As an innovative cannabis company, we want a business card that is not only visually appealing but also serves as a representation of who we are and what we stand for.

Project Scope: Design a double-sided business card that integrates our brand identity and core values. Incorporate our key brand elements, ensuring a sleek and contemporary aesthetic. Visually reflect our core values (Mission, Story, Values, Impact) in a way that is engaging yet professional.

Target Market(s)

Vendors, third parties,

Contact Information for Business Card

Contact details (name, title, email, phone, website, etc.)

Font styles to use
Other font styles liked:
• Caslon, Centra

Colors

Designer to choose colors to be used in the design.

Requirements
Must have
• Pavrel.com logo and branding A creative yet clean way to integrate our core values (Mission, Story, Values, Impact) Modern typography and a well-structured layout
Nice to have
• forest green, grey, white, black
Should not have
• references to marijuana, leafs, plants, or related product

```html
<!DOCTYPE html>
<html lang="en">
<head>
<meta charset="utf-8">
<title>Pavrel Business Card</title>
<link rel="stylesheet" href="https://fonts.googleapis.com/css2?family=Poppins:wght@400;600;700;800&display=swap">
<style>
  :root {
    --forest: #16391c;
    --forest-deep: #0f2716;
    --forest-mid: #1b4222;
    --forest-light: #2f7a3a;
    --paper: #ffffff;
    --ink: #1c1c1c;
    --rule: #9a9a9a;
    --stage: #1f1f1f;
  }
  * { box-sizing: border-box; margin: 0; padding: 0; }
  html, body {
    width: 1200px; height: 1108px; overflow: hidden;
    background: var(--stage);
    font-family: "Poppins", sans-serif;
  }
  .spread {
    position: relative; width: 1200px; height: 1108px;
    display: flex; justify-content: center; align-items: center; gap: 70px;
  }
  .card {
    width: 420px; height: 680px; border-radius: 26px;
    position: relative; overflow: hidden;
  }
  .card-front {
    background: var(--paper);
    display: flex; flex-direction: column; align-items: center;
  }
  .wordmark {
    margin-top: 90px;
    font-weight: 800; font-size: 88px; letter-spacing: -2px;
    color: var(--forest); line-height: 1;
  }
  .identity { margin-top: auto; text-align: center; }
  .person-name {
    font-weight: 700; font-size: 30px; color: var(--forest);
    letter-spacing: 0.5px; line-height: 1.1;
  }
  .person-title {
    font-weight: 400; font-size: 17px; color: var(--ink);
    letter-spacing: 1px; margin-top: 2px;
  }
  .contact-divider {
    display: flex; align-items: center; gap: 8px;
    width: 300px; margin: 16px auto 10px;
  }
  .contact-divider .rule { flex: 1; height: 1px; background: var(--rule); }
  .icon-box {
    width: 32px; height: 32px; border-radius: 4px;
    background: var(--forest);
    display: flex; align-items: center; justify-content: center;
  }
  .contact-list {
    list-style: none; text-align: center; margin-bottom: 70px;
    font-size: 20px; color: var(--ink); line-height: 1.4;
  }
  .contact-list strong { color: var(--forest); font-weight: 600; }
  .card-back { background: var(--forest-mid); }
  .pattern-field {
    position: absolute; inset: 0;
    background:
      linear-gradient(125deg, rgba(0,0,0,0) 35%, rgba(70,150,80,0.28) 62%, rgba(0,0,0,0) 78%),
      linear-gradient(160deg, var(--forest-mid) 0%, var(--forest) 45%, var(--forest-deep) 100%);
  }
  .pattern-sheen {
    position: absolute; inset: 0;
    background: radial-gradient(ellipse 70% 45% at 90% 25%, rgba(60,140,70,0.35), rgba(0,0,0,0) 70%);
  }
  .back-mark {
    position: absolute; left: 50%; top: 515px; transform: translateX(-50%);
    font-weight: 800; font-size: 34px; color: var(--paper); letter-spacing: -0.5px;
  }
</style>
</head>
<body>
  <main class="spread">
    <section class="card card-front">
      <div class="wordmark">PAVREL</div>
      <div class="identity">
        <p class="person-name">DANIEL CARTER</p>
        <p class="person-title">MANAGING DIRECTOR</p>
        <div class="contact-divider">
          <span class="rule"></span>
          <span class="icon-box">
            <svg width="20" height="20" viewBox="0 0 24 24" fill="none" stroke="#fff" stroke-width="2" stroke-linecap="round" stroke-linejoin="round"><path d="M5 4h4l2 5-2.5 1.5a11 11 0 0 0 5 5L15 13l5 2v4a2 2 0 0 1-2 2A16 16 0 0 1 3 6a2 2 0 0 1 2-2"/></svg>
          </span>
          <span class="icon-box">
            <svg width="20" height="20" viewBox="0 0 24 24" fill="none" stroke="#fff" stroke-width="2" stroke-linejoin="round"><rect x="3" y="5" width="18" height="14" rx="1"/><path d="M3 6l9 7 9-7"/></svg>
          </span>
          <span class="icon-box">
            <svg width="20" height="20" viewBox="0 0 24 24" fill="none" stroke="#fff" stroke-width="2"><circle cx="12" cy="12" r="9"/><path d="M3 12h18M12 3a14 14 0 0 1 0 18M12 3a14 14 0 0 0 0 18"/></svg>
          </span>
          <span class="rule"></span>
        </div>
        <ul class="contact-list">
          <li>044-555 210 347</li>
          <li>hello@pavrel.com</li>
          <li>www.<strong>pavrel</strong>.com</li>
        </ul>
      </div>
    </section>
    <section class="card card-back">
      <div class="pattern-field" role="img" aria-label="Tone-on-tone repeated brand name pattern in diagonal rows across a forest green field, with a lighter green sheen toward the upper right">
        <div class="pattern-sheen"></div>
      </div>
      <div class="back-mark">PAVREL</div>
    </section>
  </main>
</body>
</html>
```